Luxury Business Card Design for High-End Window Treatments

Gilded Slatworks
Custom Plantation Shutters & Architectural Shading Systems

⸻

BACK

Daniel Trevick
Owner

Custom Interior & Exterior Window Treatments

919-555-0148
gildedslatworks.com

I have included a picture that I’m hoping we can use on the back, but I’m also wondering if you can get rid of the ladder? Should we get rid of shutters , shades and blinds underneath Gilded Slatworks?

Target Market(s)

High-end residential homeowners, custom home builders, architects, interior designers, and luxury renovation clients seeking premium plantation shutters and motorized architectural shading systems.

Industry/Entity Type

Custom Window treatments

Contact Information for Business Card

Front Gilded Slatworks Custom Plantation Shutters Motorized Architectural Shading Systems BACK Daniel Trevick Owner 919-555-0148 GildedSlatworks.com Custom Interior & Exterior Window Treatments By Appointment

Requirements
Nice to have
• Not 100% sure on nice to halves or the color but you can definitely check out my website to get a better understanding of what I’m trying to do

```html
<!DOCTYPE html>
<html lang="en">
<head>
<meta charset="utf-8">
<title>Gilded Slatworks – Business Card</title>
<link rel="stylesheet" href="https://fonts.googleapis.com/css2?family=Poppins:wght@400;500;600&display=swap">
<style>
  :root {
    --bg: #2a2a2a;
    --card: #141414;
    --gold: #c9a54a;
    --gold-soft: #b8943c;
    --white: #f2f2f2;
    --sky: #6a9fd8;
    --roof: #4a4f55;
  }
  * { margin: 0; padding: 0; box-sizing: border-box; }
  html, body { width: 1200px; height: 875px; overflow: hidden; }
  body {
    background: var(--bg);
    font-family: "Poppins", sans-serif;
    display: flex;
    flex-direction: column;
    align-items: center;
    justify-content: center;
    gap: 25px;
  }
  .card {
    position: relative;
    width: 700px;
    height: 400px;
    background: var(--card);
    border-radius: 22px;
    overflow: hidden;
    border-bottom: 6px solid var(--gold);
  }
  .brand-name {
    color: var(--gold);
    font-weight: 500;
    line-height: 1.05;
  }
  .card-front .brand-name {
    position: absolute;
    left: 0; right: 0; top: 50%;
    transform: translateY(-50%);
    text-align: center;
    font-size: 64px;
  }
  .card-back .brand-name {
    position: absolute;
    left: 60px; top: 120px;
    font-size: 40px;
  }
  .photo-frame {
    position: absolute;
    left: 380px; top: 40px;
    width: 290px; height: 300px;
  }
  .photo {
    position: absolute;
    left: 30px; top: 0;
    width: 260px; height: 260px;
    border-radius: 40px;
    background: linear-gradient(160deg, var(--sky) 0%, #8fb3c9 35%, var(--roof) 60%, #2f3338 100%);
  }
  .frame-line { position: absolute; left: 0; top: 0; }
  .contact {
    position: absolute;
    left: 60px; top: 255px;
    color: var(--white);
  }
  .person-name { color: var(--gold); font-weight: 600; font-size: 24px; line-height: 1.1; }
  .person-role { font-size: 14px; margin-bottom: 12px; }
  .contact-row { display: flex; align-items: center; gap: 10px; font-size: 15px; line-height: 1.6; }
  .contact-row.phone { font-weight: 600; }
  .contact-row svg { flex: none; }
</style>
</head>
<body>
  <section class="card card-front">
    <p class="brand-name">Gilded<br>Slatworks</p>
  </section>

  <section class="card card-back">
    <p class="brand-name">Gilded<br>Slatworks</p>

    <div class="photo-frame">
      <svg class="frame-line" width="290" height="300" viewBox="0 0 290 300">
        <path d="M12 110 Q0 116 0 140 L0 296 L250 296 Q286 296 286 260 L286 230" fill="none" stroke="var(--gold)" stroke-width="3"/>
      </svg>
      <div class="photo" role="img" aria-label="Photo of a covered porch with exterior shades under tall pine trees"></div>
    </div>

    <div class="contact">
      <p class="person-name">Daniel Trevick</p>
      <p class="person-role">Owner</p>
      <p class="contact-row phone">
        <svg width="14" height="14" viewBox="0 0 24 24"><path fill="var(--gold)" d="M6.6 10.8a15 15 0 0 0 6.6 6.6l2.2-2.2c.3-.3.7-.4 1-.2 1.1.4 2.3.6 3.6.6.6 0 1 .4 1 1V20c0 .6-.4 1-1 1A17 17 0 0 1 3 4c0-.6.4-1 1-1h3.5c.6 0 1 .4 1 1 0 1.3.2 2.5.6 3.6.1.3 0 .7-.2 1z"/></svg>
        919-555-0148
      </p>
      <p class="contact-row">
        <svg width="14" height="14" viewBox="0 0 24 24"><circle cx="12" cy="12" r="10" fill="none" stroke="var(--gold)" stroke-width="2.5"/><path d="M2 12h20M12 2c3 3 3 17 0 20M12 2c-3 3-3 17 0 20" fill="none" stroke="var(--gold)" stroke-width="2"/></svg>
        gildedslatworks.com
      </p>
    </div>
  </section>
</body>
</html>
```